I need a flyer made , the flyer can be one page or two pages or three pages . I will be posting this on Instagram and social media platforms. I am a luxury home builder , I am looking to hire a construction project manager . Below are some examples and ideas what can be on the flyer

We’re looking for a construction project manager who’s passionate about building luxury homes at the highest standards
We’re hiring construction project manager
* Experience 5+ years in residential project management with a strong portfolio of completed homes.
* location : Bergen County NJ
* excellent leadership skills, leads teams with confidence and clarity
* communicates seamlessly with architects , engineers, designers and clients
*knows how to manage budgets and timelines without compromising quality
*solves problems with a positive solution first mindset
* pays attention to every detail because in luxury the small things are the big things

Apply now , link in bio or DM to connect.

My logo is attached, my web site www.velstridebuilders.com
My style is modern but still warm and inviting. I like a clean classy look .

Please don’t add any images of chairs or people to the flyer , I do not want people on my flyer. Do not add standard images of offices and houses , we are luxury builders , we build homes over 2 million dollars. Keep a classy , simple modern look . High end .

You can add a white hard hat with my logo on it for a image , this is a suggestion does not have to be on my flyer ,

```html
<!DOCTYPE html>
<html lang="en">
<head>
<meta charset="UTF-8">
<title>Hiring – Construction Project Manager</title>
<link href="https://fonts.googleapis.com/css2?family=Poppins:wght@400;500;600;800&family=Oswald:wght@500;600&family=Roboto+Condensed:wght@700&display=swap" rel="stylesheet">
<style>
  :root {
    --stage: #8a8a8a;
    --ink: #1c1c1c;
    --ink-soft: #2a2a2a;
    --sand: #f2d9ad;
    --mist: #e2e3e7;
    --white: #ffffff;
  }
  * { margin: 0; padding: 0; box-sizing: border-box; }
  html, body { width: 1200px; height: 1194px; overflow: hidden; background: var(--stage); }
  body { position: relative; font-family: "Poppins", sans-serif; }

  .flyer {
    position: absolute; left: 114px; top: 111px; width: 972px; height: 972px;
    background: var(--ink); overflow: hidden;
    box-shadow: 0 0 18px rgba(0,0,0,.35);
  }
  .site-backdrop {
    position: absolute; inset: 0 0 60px 0;
    background: linear-gradient(180deg, #2b2b2b 0%, #262626 45%, #1e1e1e 100%);
  }
  .pm-photo {
    position: absolute; left: 502px; top: 209px; width: 448px; height: 712px;
    background: radial-gradient(ellipse at 60% 45%, #c9ccd3 0%, #8d9099 35%, #3a3a3c 70%, rgba(30,30,30,0) 100%);
  }

  .headline-top {
    position: absolute; left: 57px; top: 44px;
    font-weight: 600; font-size: 104px; line-height: 1; color: var(--mist); letter-spacing: -1px;
  }
  .headline-main {
    position: absolute; left: 54px; top: 122px;
    font-weight: 800; font-size: 140px; line-height: 1; color: var(--sand); letter-spacing: -3px;
  }
  .role-tag {
    position: absolute; left: 108px; top: 268px; width: 482px; height: 58px;
    background: var(--white); transform: rotate(-5deg);
    display: flex; align-items: center; justify-content: center;
    font-family: "Roboto Condensed", sans-serif; font-weight: 700; font-size: 32px; color: var(--ink);
  }
  .role-icon { position: absolute; left: 84px; top: 244px; width: 48px; height: 46px; }

  .tagline {
    position: absolute; left: 60px; top: 372px;
    font-weight: 500; font-size: 24px; letter-spacing: 4.6px; color: var(--white);
  }
  .location {
    position: absolute; left: 60px; top: 414px; height: 50px; display: flex;
  }
  .location-label {
    width: 186px; background: var(--mist); color: var(--ink);
    font-weight: 500; font-size: 26px; display: flex; align-items: center; justify-content: center;
  }
  .location-value {
    width: 345px; background: var(--sand); color: var(--ink);
    font-weight: 600; font-size: 30px; display: flex; align-items: center; padding-left: 22px;
  }

  .requirements { position: absolute; left: 60px; top: 505px; list-style: none; width: 470px; }
  .requirements li {
    position: relative; padding-left: 32px; margin-bottom: 16px;
    font-size: 18px; line-height: 22.5px; color: var(--white);
  }
  .requirements li svg { position: absolute; left: 0; top: 5px; width: 16px; height: 16px; }
  .requirements em { font-style: normal; color: var(--sand); }

  .apply {
    position: absolute; left: 102px; top: 837px; width: 192px; height: 60px;
    background: var(--sand); color: var(--ink);
    font-family: "Oswald", sans-serif; font-weight: 600; font-size: 40px; line-height: 60px;
    padding-left: 24px; letter-spacing: -.5px;
  }
  .apply-icon { position: absolute; left: 62px; top: 830px; width: 64px; height: 70px; }
  .connect { position: absolute; left: 310px; top: 838px; color: var(--white); }
  .connect-line { font-weight: 500; font-size: 22px; line-height: 30px; }
  .handle { display: flex; align-items: center; gap: 12px; font-size: 23px; line-height: 30px; margin-top: 2px; }
  .handle-dot { width: 22px; height: 22px; border-radius: 50%; background: var(--sand); }

  .brand {
    position: absolute; left: 664px; top: 62px; width: 252px; text-align: center;
    font-weight: 400; color: var(--white); line-height: 1;
  }
  .brand-name { font-size: 38px; letter-spacing: 2px; }
  .brand-sub { font-size: 12px; letter-spacing: 2px; margin-top: 14px; }

  .badge { position: absolute; left: 626px; top: 610px; width: 268px; height: 268px; }
  .badge-text {
    position: absolute; left: 636px; top: 650px; width: 248px; text-align: center; color: var(--ink);
  }
  .badge-title { font-family: "Oswald", sans-serif; font-weight: 600; font-size: 34px; line-height: 40px; }
  .badge-years { font-family: "Oswald", sans-serif; font-weight: 600; font-size: 32px; line-height: 44px; }
  .badge-years b { font-size: 44px; }
  .badge-copy { font-weight: 500; font-size: 15.5px; line-height: 19.5px; margin-top: 2px; }

  .website {
    position: absolute; left: 648px; top: 880px; font-weight: 500; font-size: 17px;
    letter-spacing: .6px; color: var(--white);
  }
  .website span { color: var(--sand); }
</style>
</head>
<body>
  <main class="flyer">
    <div class="site-backdrop" role="img" aria-label="Dark, faded photo of a timber-framed luxury home under construction"></div>
    <div class="pm-photo" role="img" aria-label="Project manager in a white hard hat and white shirt holding a clipboard"></div>

    <div class="brand">
      <div class="brand-name">VELSTRIDE</div>
      <div class="brand-sub">builders</div>
    </div>

    <h1 class="headline-top">WE’RE</h1>
    <div class="headline-main">HIRING!</div>

    <svg class="role-icon" viewBox="0 0 48 46" fill="none" stroke="#f2d9ad" stroke-width="3" stroke-linejoin="round">
      <path d="M6 28 L30 12 L36 32 L10 36 Z"/>
      <path d="M12 36 L16 44 L22 42 L19 35"/>
      <path d="M36 8 L40 3 M40 16 L46 14 M32 4 L32 0"/>
    </svg>
    <div class="role-tag">Construction Project Manager</div>

    <p class="tagline">Build Luxury. Lead Excellence.</p>

    <div class="location">
      <div class="location-label">LOCATION</div>
      <div class="location-value">Bergen County, NJ</div>
    </div>

    <ul class="requirements">
      <li><svg viewBox="0 0 16 16"><circle cx="8" cy="8" r="8" fill="#f2d9ad"/><path d="M4.5 8.2 L7 10.5 L11.5 5.8" stroke="#1c1c1c" stroke-width="2" fill="none"/></svg><em>Excellent leadership skills,</em> leads teams with confidence and clarity</li>
      <li><svg viewBox="0 0 16 16"><circle cx="8" cy="8" r="8" fill="#f2d9ad"/><path d="M4.5 8.2 L7 10.5 L11.5 5.8" stroke="#1c1c1c" stroke-width="2" fill="none"/></svg><em>Communicates seamlessly</em> with architects engineers, designers and clients</li>
      <li><svg viewBox="0 0 16 16"><circle cx="8" cy="8" r="8" fill="#f2d9ad"/><path d="M4.5 8.2 L7 10.5 L11.5 5.8" stroke="#1c1c1c" stroke-width="2" fill="none"/></svg><em>Knows how to manage</em> budgets and timelines without compromising quality</li>
      <li><svg viewBox="0 0 16 16"><circle cx="8" cy="8" r="8" fill="#f2d9ad"/><path d="M4.5 8.2 L7 10.5 L11.5 5.8" stroke="#1c1c1c" stroke-width="2" fill="none"/></svg><em>Solves problems</em> with a positive<br>solution first mindset</li>
      <li><svg viewBox="0 0 16 16"><circle cx="8" cy="8" r="8" fill="#f2d9ad"/><path d="M4.5 8.2 L7 10.5 L11.5 5.8" stroke="#1c1c1c" stroke-width="2" fill="none"/></svg><em>Pays attention to every detail</em> because in luxury the small things are the big things</li>
    </ul>

    <div class="apply">APPLY NOW</div>
    <svg class="apply-icon" viewBox="0 0 64 70" fill="#1c1c1c" stroke="#f2d9ad" stroke-width="3.5" stroke-linejoin="round">
      <path d="M6 46 L38 16 L50 44 L14 56 Z"/>
      <path d="M16 55 L22 66 L30 63 L26 52" fill="none"/>
      <path d="M46 12 L52 5 M52 24 L60 22 M42 6 L42 1" fill="none"/>
    </svg>

    <div class="connect">
      <div class="connect-line">Link in bio or DM to connect</div>
      <div class="handle"><span class="handle-dot"></span>velstridebuilders</div>
    </div>

    <svg class="badge" viewBox="0 0 268 268">
      <defs><polygon id="spike" points="134,2 121,30 147,30" fill="#f2d9ad"/></defs>
      <circle cx="134" cy="134" r="112" fill="#f2d9ad"/>
      <use href="#spike"/>
      <use href="#spike" transform="rotate(18 134 134)"/>
      <use href="#spike" transform="rotate(36 134 134)"/>
      <use href="#spike" transform="rotate(54 134 134)"/>
      <use href="#spike" transform="rotate(72 134 134)"/>
      <use href="#spike" transform="rotate(90 134 134)"/>
      <use href="#spike" transform="rotate(108 134 134)"/>
      <use href="#spike" transform="rotate(126 134 134)"/>
      <use href="#spike" transform="rotate(144 134 134)"/>
      <use href="#spike" transform="rotate(162 134 134)"/>
      <use href="#spike" transform="rotate(180 134 134)"/>
      <use href="#spike" transform="rotate(198 134 134)"/>
      <use href="#spike" transform="rotate(216 134 134)"/>
      <use href="#spike" transform="rotate(234 134 134)"/>
      <use href="#spike" transform="rotate(252 134 134)"/>
      <use href="#spike" transform="rotate(270 134 134)"/>
      <use href="#spike" transform="rotate(288 134 134)"/>
      <use href="#spike" transform="rotate(306 134 134)"/>
      <use href="#spike" transform="rotate(324 134 134)"/>
      <use href="#spike" transform="rotate(342 134 134)"/>
    </svg>
    <div class="badge-text">
      <div class="badge-title">EXPERIENCE</div>
      <div class="badge-years"><b>5</b>+ YEARS</div>
      <div class="badge-copy">in residential project<br>management with a<br>strong portfolio of<br>completed homes.</div>
    </div>

    <div class="website">www.<span>velstridebuilders</span>.com</div>
  </main>
</body>
</html>
```